Innovative automotive company needs some flat designs

Hi there. This is your project brief that will tell you everything you need to know. We want to create a Facebook ad that tells a story about the benefits of using our platform. We have a compelling story. We have the words. Now we need the graphics.
Requirements:
Our company's brand identity has the following three elements, futuristic, premium and minimalistic. The design has to be like this too.
Our colour scheme is RGB (255,255,255), 73,225,245, and 5, 7, 9.
Here's our company's landing page. From there you may take a look at our app too.
www.velmorix.io
We have a great story to tell. Help us make it eye-catching. And engaging.
Here are the 4 points/images we want to bring across. Words in brackets should be included in the images.
Words should only take up AT MOST 20% of the space.
THERE SHOULD BE 4 IMAGES (1 FOR EACH POINT). PLEASE DO NOT USE THE ICONS THAT WE HAVE ON OUR WEBSITE. You can refer to the attached for reference. This is the kind of format that we want but the style should be suited to our company brand identity and colour scheme.
Each image should be 600 x 600 pixels
1) Quality Assurance
(3-tier screening to select partner workshops of all expertise. Regular audit and mystery shopping to ensure quality.)
2) Save time and effort
(For each requests, our system chooses the best offers and send them to you. Compare job scope, price, reviews, duration and others at a glance.)
3) No overcharging, no redundant repairs
(Job scope is pre-agreed through the app. Any changes have to be documented.
With these records, our in-house technical expertise and data analytics will identify bad behaviour.)
4) Community Reviews
(Reviews from consumers after each job is completed. Ensure high standards consistently.)
Updates
Industry/Entity Type
Automotive
Look and feel

```html
<!DOCTYPE html>
<html lang="en">
<head>
<meta charset="utf-8">
<title>Velmorix – Quality Assurance</title>
<link href="https://fonts.googleapis.com/css2?family=Michroma&display=swap" rel="stylesheet">
<style>
  :root {
    --brand-white: #ffffff;
    --brand-cyan: #49e1f5;
    --brand-cyan-soft: #7cecfb;
    --brand-ink: #050709;
    --panel-top: #1a232d;
    --panel-bottom: #0c1218;
    --rule: #3a444e;
    --body-text: #e9eef2;
  }
  html, body {
    margin: 0;
    padding: 0;
    width: 1200px;
    height: 1200px;
    overflow: hidden;
    background: var(--brand-white);
  }
  .ad {
    position: relative;
    width: 1200px;
    height: 1200px;
    font-family: "Michroma", sans-serif;
    color: var(--brand-white);
  }
  .ad__panel {
    position: absolute;
    inset: 0;
  }
  .brand-name {
    position: absolute;
    top: 108px;
    right: 60px;
    margin: 0;
    font-size: 58px;
    font-weight: 400;
    letter-spacing: 10px;
    color: var(--brand-white);
    line-height: 1;
  }
  .feature-icon {
    position: absolute;
    left: 140px;
    top: 290px;
    width: 240px;
    height: 210px;
  }
  .feature {
    position: absolute;
    left: 292px;
    top: 572px;
    width: 820px;
  }
  .feature__title {
    margin: 0 0 22px;
    font-size: 42px;
    font-weight: 400;
    font-variant: small-caps;
    letter-spacing: 2px;
    line-height: 1.1;
    color: var(--brand-white);
  }
  .feature__title-initial {
    color: var(--brand-cyan);
  }
  .feature__text {
    margin: 0;
    font-size: 27px;
    font-variant: small-caps;
    line-height: 31px;
    letter-spacing: 1px;
    color: var(--body-text);
  }
  .divider {
    position: absolute;
    left: 150px;
    top: 882px;
    width: 910px;
    height: 2px;
    background: var(--rule);
  }
</style>
</head>
<body>
  <main class="ad">
    <svg class="ad__panel" width="1200" height="1200" viewBox="0 0 1200 1200" role="img" aria-label="Dark, moody close-up photograph of a car interior and dashboard">
      <defs>
        <linearGradient id="panelShade" x1="0" y1="0" x2="0.4" y2="1">
          <stop offset="0" stop-color="var(--panel-top)"/>
          <stop offset="0.55" stop-color="#141c24"/>
          <stop offset="1" stop-color="var(--panel-bottom)"/>
        </linearGradient>
      </defs>
      <polygon points="0,0 1200,0 1200,960 1166,1200 80,1200 0,1170" fill="url(#panelShade)"/>
    </svg>

    <p class="brand-name">VELMORIX</p>

    <svg class="feature-icon" viewBox="0 0 240 210" aria-hidden="true">
      <rect x="48" y="40" width="186" height="140" rx="8" fill="var(--brand-cyan)" transform="rotate(-8 141 110)"/>
      <rect x="14" y="36" width="190" height="138" rx="6" fill="var(--brand-cyan-soft)" stroke="var(--brand-white)" stroke-width="6"/>
      <g fill="none" stroke="var(--brand-ink)" stroke-width="6" stroke-linejoin="round">
        <circle cx="108" cy="88" r="24"/>
        <polyline points="92,106 92,148 108,136 124,148 124,106"/>
      </g>
    </svg>

    <section class="feature">
      <h1 class="feature__title"><span class="feature__title-initial">Q</span>uality Assurance</h1>
      <p class="feature__text">3-tier screening to select partner workshops of all expertise. Regular audit and mystery shopping to ensure quality.</p>
    </section>

    <div class="divider"></div>
  </main>
</body>
</html>
```